San Francisco Leading Consulting firm - 47Vora Web Design Project

•Create a Web Design
•Uncoded webpage layout design
•2 Pages Design - Homepage + Interior Page

Task Description
Hello, we're looking for a re-design our current website www.47vora-example.com

we have a sample mockup design @

http://47vora.pubtrellis-example.org/

This shows the layout that we like and also a sample of 6 pictures that would change based on where you mouse over..

6 pictures HOME design needs to be included.

SMART
THOUGHTFUL
FLEXIBLE
CREATIVE SERVICES
TECHNICAL SERVICES
PARTNERS

sites we like:

http://www.melvanadvisory-example.com/Home.cfm?id=Home
http://www.plinthworks-example.com/index.html

Our company can be best described as: 100+ employees, cutting-edge, depandable, innovative, strong, smart.

Our Primary focus is: IT Consulting Services and Creative Design services

47Vora LLC is a consulting firm providing creative design, business and technology solutions to both private and public interests.

Established in 1996, 47Vora is a San Francisco based company providing specialists for a range of business needs including:

Creative Design Services
•Print
•Logo Design
•Website Design
•Illustration

and

Business and Technology solutions

•Application Software and Web Development
•Business Process Re-Design (BPR)
•Business/Systems Analysis and Requirement Documentation
•Mentoring and Training
•Network/Hardware Installation Services
•System Design and Architecture
•Vendor Management
•Docuvault Architecture and Implementation

our sample mockup site:

Reason: Due to holiday season, we're not available to work with designers and finilize our design.  

Thank you very much for submitting your design.

We appreciate your time and creativity.   Since, our office is currently closed for holidays, we will be reviewing it in details next week and will make our decision as soon as possible.

It would be great if you could submit any of your changes by Wed next week, so it would be part of our reviews. 

Please see updated wireframe under attachments:  we have some minor updates to our wireframe that we would like you to update your designs, if possible.  

We also encorouge you not to use our standard wireframe and come up with more unique designs.   Everything would be considered when we review your design.

 

Ringmark Market(s)

Creative services and professional services clients, including government agencies

Industry/Entity Type

Business

Requirements
Must have
• Clean, professional look, easy navigation

```html
<!DOCTYPE html>
<html lang="en">
<head>
<meta charset="utf-8">
<title>47Vora — Consulting, Creative &amp; Technical Services</title>
<link rel="stylesheet" href="https://fonts.googleapis.com/css2?family=Arimo:wght@400;700&family=Roboto+Condensed:wght@400;700&display=swap">
<style>
  :root{
    --brand-blue:#0a8fc8;
    --brand-blue-light:#3fb6ee;
    --ink:#333333;
    --ink-soft:#555555;
    --client-grey:#8a8a8a;
    --rule:#d6d6d6;
    --card-border:#b9b9b9;
    --paper:#ffffff;
    --slide-dark:#2b2b2b;
  }
  *{margin:0;padding:0;box-sizing:border-box}
  html,body{width:1200px;height:960px;overflow:hidden;background:var(--paper);font-family:"Arimo",Helvetica,Arial,sans-serif;color:var(--ink)}
  .page{position:relative;width:1200px;height:960px}

  /* header */
  .site-header{position:absolute;left:0;top:0;width:1200px;height:92px;background:var(--paper);border-bottom:2px solid var(--brand-blue)}
  .brand{position:absolute;left:170px;top:16px;display:flex;align-items:center;gap:10px}
  .brand-mark{width:28px;height:28px;border-radius:50%;background:var(--brand-blue-light)}
  .brand-name{font-size:30px;letter-spacing:3px;color:var(--ink-soft);font-weight:400}
  .brand-est{position:absolute;left:266px;top:79px;font-size:12px;font-weight:700;color:var(--brand-blue);letter-spacing:.3px}
  .main-nav{position:absolute;left:383px;top:38px;display:flex}
  .main-nav a{font-size:12px;font-weight:700;color:var(--ink-soft);text-decoration:none;padding:0 10px;line-height:18px;border-left:1px solid var(--brand-blue)}
  .main-nav a:first-child{border-left:none}
  .main-nav a:nth-child(3){border-left-color:#444}
  .main-nav a:nth-child(5){border-left-color:#444}
  .contact{position:absolute;left:929px;top:12px;font-size:12px;line-height:18px;color:var(--ink)}
  .contact .hl{color:var(--brand-blue);font-weight:700}

  /* hero */
  .hero-backdrop{position:absolute;left:0;top:92px;width:1200px;height:528px;
    background:linear-gradient(180deg,#d9d9d9 0%,#bdbdbd 45%,#8d8d8d 80%,#a5a5a5 100%)}
  .slider{position:absolute;left:118px;top:137px;width:960px;height:400px;border-top:6px solid var(--brand-blue);border-bottom:5px solid var(--brand-blue);border-radius:3px}
  .slide-art{position:absolute;left:0;top:0;width:960px;height:343px;
    background:linear-gradient(90deg,#7b95ae 0%,#a6c2dc 25%,#94b1cc 55%,#7f98b1 100%)}
  .slide-bulb{position:absolute;left:610px;top:40px;width:190px;height:300px;border-radius:95px 95px 40px 40px;
    background:radial-gradient(circle at 50% 35%,#f2f4f5 0%,#c9d3dc 55%,rgba(150,170,190,0) 72%)}
  .slide-title{position:absolute;left:110px;top:88px;font-family:"Arimo",Helvetica,sans-serif;font-weight:700;font-size:50px;color:#fff;line-height:1;text-shadow:1px 2px 2px rgba(0,0,0,.35)}
  .slide-sub{position:absolute;left:110px;top:140px;font-family:"Roboto Condensed",Arial Narrow,sans-serif;font-weight:700;font-size:23px;color:#fff;letter-spacing:.3px;text-shadow:1px 2px 2px rgba(0,0,0,.35)}
  .slide-arrow{position:absolute;top:150px}
  .slide-arrow.prev{left:18px}
  .slide-arrow.next{left:912px}
  .slide-bar{position:absolute;left:0;top:343px;width:960px;height:46px;background:rgba(30,30,30,.85)}
  .dots{position:absolute;left:401px;top:15px;display:flex;gap:13px}
  .dots span{width:15px;height:15px;border-radius:50%;background:#fff}
  .dots span.active{background:var(--brand-blue-light)}

  /* clients */
  .clients{position:absolute;left:120px;top:630px;width:960px;height:77px;border-bottom:1px solid var(--rule)}
  .clients-label{position:absolute;left:6px;top:10px;font-size:20px;font-weight:700;line-height:24px;color:var(--ink)}
  .clients-chevron{position:absolute;left:114px;top:14px}
  .client{position:absolute;top:22px;display:flex;align-items:center;gap:6px;font-size:17px;font-weight:700;color:var(--client-grey)}
  .client i{display:block;width:16px;height:16px;border-radius:50%;background:var(--client-grey)}

  /* service cards */
  .card{position:absolute;top:735px;width:280px;height:99px;border:1px solid var(--card-border);border-radius:4px;overflow:hidden;background:var(--paper)}
  .card-title{position:absolute;left:6px;top:4px;font-size:15px;color:var(--ink-soft)}
  .card-art{position:absolute}
  .card-corner{position:absolute;right:0;bottom:0}

  /* footer */
  .site-footer{position:absolute;left:120px;top:860px;width:960px;border-top:1px solid var(--rule)}
  .copyright{position:absolute;left:2px;top:17px;font-size:12px;color:var(--ink)}
  .footer-nav{position:absolute;right:7px;top:18px;display:flex;gap:30px}
  .footer-nav a{font-size:12px;font-weight:700;color:var(--ink);text-decoration:none}
</style>
</head>
<body>
<div class="page">

  <header class="site-header">
    <div class="brand"><span class="brand-mark"></span><span class="brand-name">47VORA</span></div>
    <div class="brand-est">ESTABLISHED 1996</div>
    <nav class="main-nav">
      <a href="#">Company</a>
      <a href="#">Creative Services</a>
      <a href="#">Technical Services</a>
      <a href="#">Partners</a>
      <a href="#">Contact Us</a>
    </nav>
    <address class="contact" style="font-style:normal">
      2287 Alder St, Ste 410<br>
      San Francisco, CA 94199<br>
      <span class="hl">415-555-0147</span><br>
      <span class="hl">info@47vora-example.com</span>
    </address>
  </header>

  <div class="hero-backdrop" role="img" aria-label="Black and white aerial photo of the San Francisco skyline"></div>

  <section class="slider">
    <div class="slide-art" role="img" aria-label="Photo of a glowing light bulb on a blue background"></div>
    <div class="slide-bulb" role="img" aria-label="Light bulb"></div>
    <h1 class="slide-title">SMART</h1>
    <p class="slide-sub">WE DON'T BELIEVE IN THE TERM 'OVERQUALIFIED'</p>
    <svg class="slide-arrow prev" width="34" height="56" viewBox="0 0 34 56"><polyline points="28,4 8,28 28,52" fill="none" stroke="#fff" stroke-width="8"/></svg>
    <svg class="slide-arrow next" width="34" height="56" viewBox="0 0 34 56"><polyline points="6,4 26,28 6,52" fill="none" stroke="#fff" stroke-width="8"/></svg>
    <div class="slide-bar">
      <div class="dots"><span class="active"></span><span></span><span></span><span></span><span></span><span></span></div>
    </div>
  </section>

  <section class="clients">
    <h2 class="clients-label">Featured<br>Clients</h2>
    <svg class="clients-chevron" width="22" height="36" viewBox="0 0 22 36"><polyline points="4,2 17,18 4,34" fill="none" stroke="var(--brand-blue)" stroke-width="6"/></svg>
    <span class="client" style="left:162px"><i></i>Ringmark</span>
    <span class="client" style="left:265px">Lumora</span>
    <span class="client" style="left:330px">Kestro</span>
    <span class="client" style="left:385px">Halvane</span>
    <span class="client" style="left:470px">Brixa</span>
    <span class="client" style="left:570px">Tellwave</span>
    <span class="client" style="left:660px">Norvik</span>
    <span class="client" style="left:750px">Fieldhart</span>
    <span class="client" style="left:865px">Fizzco</span>
  </section>

  <article class="card" style="left:120px">
    <h3 class="card-title">Creative Services</h3>
    <div class="card-art" role="img" aria-label="Colourful abstract swirl illustration" style="left:80px;top:26px;width:150px;height:80px;border-radius:60px 60px 0 0;background:linear-gradient(135deg,#d35ad6,#f1d23c 50%,#3fc2e0)"></div>
    <svg class="card-corner" width="41" height="41" viewBox="0 0 41 41"><polygon points="41,0 41,41 0,41" fill="var(--brand-blue)"/><path d="M28 22v12M22 28h12" stroke="#fff" stroke-width="2.5"/></svg>
  </article>

  <article class="card" style="left:458px">
    <h3 class="card-title">Business &amp; Technical Services</h3>
    <div class="card-art" role="img" aria-label="Illustration of metal gears" style="left:44px;top:28px;width:165px;height:75px;border-radius:40px 40px 0 0;background:linear-gradient(180deg,#cfcfcf,#8f8f8f)"></div>
    <svg class="card-corner" width="41" height="41" viewBox="0 0 41 41"><polygon points="41,0 41,41 0,41" fill="var(--brand-blue)"/><path d="M28 22v12M22 28h12" stroke="#fff" stroke-width="2.5"/></svg>
  </article>

  <article class="card" style="left:793px">
    <h3 class="card-title">Partners</h3>
    <div class="card-art" role="img" aria-label="Colourful network map of the United States" style="left:86px;top:8px;width:145px;height:80px;border-radius:8px;background:linear-gradient(135deg,#8fd3e8,#f3a3d8 50%,#b6e38a)"></div>
    <svg class="card-corner" width="41" height="41" viewBox="0 0 41 41"><polygon points="41,0 41,41 0,41" fill="var(--brand-blue)"/><path d="M28 22v12M22 28h12" stroke="#fff" stroke-width="2.5"/></svg>
  </article>

  <footer class="site-footer">
    <p class="copyright">Copyright 2011, 47Vora, LLC All rights reserved.</p>
    <nav class="footer-nav">
      <a href="#">Home</a>
      <a href="#">Company</a>
      <a href="#">Technical Services</a>
      <a href="#">Creative Services</a>
      <a href="#">Partners</a>
      <a href="#">Contact Us</a>
    </nav>
  </footer>

</div>
</body>
</html>
```